Website for enterprise software start-up

We need a new Wordpress website. We are an early stage start-up focused on mobile video technology for cellular operators. The audience is strategy, marketing and customer acquisition execs from the operators.

The purpose of the site is to act as a sales brochure and capture leads. A demo app can be downloaded from the current site, want to put that behind a contact form.

Current website is at www.velmora.tv. Similar number of pages. Looking for a clean design template, with minimal customization. Blog will remain as is.

Want to be able to modify the copy via Wordpress. Reference designs I like: quandrix.com, briskfold7metrics.com

Target Market(s)

Mobile operators and MVNOs in the US and Asia Pacific regions

Industry/Entity Type

Business Software

Coding

Coded - Design and coding required

Number of Pages Required

4 page

Font styles to use
Sans Serif

Colors
f78f20

Requirements
Must have
• Form for downloading sample apps.
• Landing page with image, Product, Blog, About, Contact
• Team page

```html
<!DOCTYPE html>
<html lang="en">
<head>
<meta charset="utf-8">
<title>Velmora Media — High Quality Mobile Engagement</title>
<link rel="stylesheet" href="https://fonts.googleapis.com/css2?family=Raleway:wght@300;400;600;700&family=Open+Sans:wght@400;600;700&display=swap">
<style>
:root{
  --orange:#e8641b;
  --orange-soft:#f78f20;
  --ink:#333333;
  --muted:#777777;
  --light:#ffffff;
  --dark:#2b2a28;
  --line:#e7e7e7;
  --field:rgba(255,255,255,0.08);
}
*{box-sizing:border-box;margin:0;padding:0}
html,body{width:1200px;height:4557px;overflow:hidden;background:#fff}
body{font-family:"Open Sans",Arial,sans-serif;color:var(--ink);position:relative}
section,header,footer{position:absolute;left:0;width:1200px;overflow:hidden}
.abs{position:absolute}
.heading{font-family:"Raleway",Arial,sans-serif;font-weight:300}

/* hero */
.hero{top:0;height:705px}
.hero-photo{position:absolute;inset:0;background:linear-gradient(180deg,#5f5e58 0%,#4a4b47 45%,#6b6a63 75%,#55544f 100%)}
.hero-shade{position:absolute;inset:0;background:rgba(0,0,0,0.25)}
.brand{position:absolute;display:flex;align-items:center;gap:12px;color:var(--light);font-family:"Raleway",Arial,sans-serif;font-weight:700}
.brand-mark{background:var(--orange);display:block}
.hero .brand{left:96px;top:42px;font-size:32px}
.hero .brand-mark{width:40px;height:40px}
.nav{position:absolute;right:150px;top:58px;display:flex;gap:74px;font-size:12px;font-weight:600;color:var(--light);letter-spacing:.5px}
.hero-title{top:282px;width:100%;text-align:center;color:var(--light);font-size:46px;font-family:"Open Sans",Arial,sans-serif;font-weight:400}
.hero-sub{top:356px;width:100%;text-align:center;color:var(--light);font-size:18px}
.btn{display:flex;align-items:center;justify-content:center;gap:8px;background:var(--orange);color:var(--light);font-weight:700;font-size:13px;letter-spacing:.5px}
.hero-btn{left:520px;top:414px;width:164px;height:44px}
.scroll-cue{left:588px;top:618px}
.side-dots{right:28px;top:305px;display:flex;flex-direction:column;gap:20px}
.side-dots span{width:8px;height:8px;border-radius:50%;background:rgba(255,255,255,.55)}
.side-dots span:first-child{background:#fff}

/* partners */
.partners{top:705px;height:175px;border-bottom:1px solid var(--line);display:flex;align-items:center;justify-content:space-around;padding:0 80px}
.partner{font-family:"Open Sans",Arial,sans-serif;font-weight:700;font-size:22px;color:#6d6d6d;display:flex;align-items:center;gap:8px}
.partner i{width:18px;height:18px;background:#8a8a8a;border-radius:50%;display:block}

/* welcome */
.welcome{top:880px;height:382px;text-align:center}
.welcome h2{position:absolute;top:18px;width:100%;font-size:44px;color:#444}
.welcome p{position:absolute;left:210px;width:780px;font-size:14px;line-height:28px;color:var(--muted)}

/* push */
.push{top:1262px;height:641px;background:linear-gradient(90deg,#3a3632,#4c4741 50%,#2f2c29);color:var(--light)}
.device{position:absolute;border-radius:34px;background:#f2f2f2;border:2px solid #d9d9d9}
.screen{position:absolute;border-radius:2px}
.push h2{left:495px;top:148px;font-size:44px;font-weight:300}
.lead{font-size:15px;line-height:26px}
.ticks{list-style:none}
.ticks li{position:relative;padding-left:30px;font-size:13px;line-height:20px;margin-bottom:22px}
.ticks li svg{position:absolute;left:0;top:3px}

/* native */
.native{top:1903px;height:620px}
.native h2{left:106px;top:150px;font-size:42px;color:#444}

/* team */
.team{top:2523px;height:502px;background:#fff}
.team h2{top:46px;width:100%;text-align:center;font-size:44px;color:#444}
.member{position:absolute;top:150px;width:200px;text-align:center}
.avatar{width:196px;height:196px;border-radius:50%;border:6px solid #f4c49a;background:linear-gradient(180deg,#c9d5df,#a9b7c2);margin:0 auto}
.member h3{font-weight:400;font-size:16px;color:#333;margin-top:28px}
.member p{font-size:12px;color:var(--muted);margin-top:6px}
.arrow{top:262px;font-family:"Raleway",Arial,sans-serif;font-weight:300;font-size:56px;color:#bbb}

/* apps */
.apps{top:3025px;height:583px;background:linear-gradient(90deg,#3c3935,#4a4640 55%,#2a2826);color:var(--light)}
.apps h2{top:86px;width:100%;text-align:center;font-size:44px}
.store{display:flex;align-items:center;gap:10px;padding-left:16px;background:var(--orange);color:#fff;font-size:10px;line-height:13px}
.store b{display:block;font-size:14px}
.field{border:1px solid rgba(255,255,255,.55);background:var(--field);font-size:12px;color:#fff;padding:12px 14px}
.submit{font-size:14px}

/* features */
.features{top:3608px;height:642px}
.features h2{left:526px;top:118px;font-size:44px;color:#444}
.features .ticks li{color:var(--muted);margin-bottom:26px}

/* footer */
.footer{top:4250px;height:307px;background:var(--orange);color:var(--light);text-align:center}
.footer .brand{left:452px;top:66px;font-size:46px}
.footer .brand-mark{width:58px;height:58px;background:#fff}
.foot-links{top:146px;width:100%;display:flex;justify-content:center;gap:26px;font-size:11px;font-weight:600}
.foot-copy{top:182px;width:100%;display:flex;justify-content:center;gap:40px;font-size:11px}
.social{top:226px;left:552px;display:flex;gap:8px}
.social span{width:28px;height:28px;border-radius:50%;background:#fff;display:block}
.foot-tag{right:50px;top:244px;font-size:11px}
</style>
</head>
<body>

<header class="hero">
  <div class="hero-photo" role="img" aria-label="Group of young friends sitting together outdoors looking at their phones"></div>
  <div class="hero-shade"></div>
  <div class="brand"><span class="brand-mark"></span>velmora</div>
  <nav class="nav"><span>PRODUCT</span><span>CONTACT</span><span>BLOG</span><span>ABOUT</span><span>LOGIN</span></nav>
  <h1 class="abs hero-title">High Quality Mobile Engagement™</h1>
  <p class="abs hero-sub">We engage mobile audiences with the right video content at the perfect moment.</p>
  <a class="abs btn hero-btn">
    <svg width="16" height="16" viewBox="0 0 16 16"><circle cx="8" cy="8" r="6.5" fill="none" stroke="#fff" stroke-width="1.6"/><path d="M8 4.5v5M5.5 7.5L8 10l2.5-2.5" fill="none" stroke="#fff" stroke-width="1.6"/></svg>
    SAMPLE APPS</a>
  <svg class="abs scroll-cue" width="24" height="56" viewBox="0 0 24 56"><rect x="2" y="2" width="20" height="34" rx="10" fill="none" stroke="#fff" stroke-width="2"/><line x1="12" y1="10" x2="12" y2="18" stroke="#fff" stroke-width="2"/><path d="M6 44l6 6 6-6" fill="none" stroke="#fff" stroke-width="2"/></svg>
  <div class="abs side-dots"><span></span><span></span><span></span><span></span></div>
</header>

<section class="partners">
  <span class="partner"><i></i>Harbor Kings</span>
  <span class="partner"><i></i>Halvern Music</span>
  <span class="partner"><i></i>Northgate</span>
  <span class="partner">BRIXCAST</span>
  <span class="partner"><i></i>Qorva</span>
  <span class="partner">ondera</span>
  <span class="partner">lumenreel</span>
</section>

<section class="welcome">
  <h2 class="heading">Welcome to Velmora</h2>
  <p style="top:128px">Velmora Media exists because video consumption is trending away from TV towards mobile, and because mobile media is trending away from pull consumption towards push consumption - where each user is notified of personalized content at the perfect moment.</p>
  <p style="top:240px">We started Velmora Media to help media publishers navigate these trends, solving the technical challenges of delivering personalized and highest quality mobile video experiences, and seizing the economic opportunity of attracting premium brand advertising.</p>
</section>

<section class="push">
  <div class="abs" style="inset:0" role="img" aria-label="Dim outdoor backdrop of a person holding a phone"></div>
  <div class="device" style="left:188px;top:90px;width:210px;height:458px">
    <div class="screen" style="left:14px;top:64px;width:178px;height:316px;background:linear-gradient(160deg,#6c5a8c,#3a5e4a)" role="img" aria-label="Animated cartoon video playing in a notification"></div>
  </div>
  <h2 class="abs heading">Push Video Notifications</h2>
  <p class="abs lead" style="left:495px;top:222px;width:560px">Personalised flawless HD videos, revealed at the perfect moment, as rich media notifications.</p>
  <ul class="abs ticks" style="left:495px;top:300px;width:640px">
    <li><svg width="14" height="12" viewBox="0 0 14 12"><path d="M1 6l4 4 8-9" fill="none" stroke="#f78f20" stroke-width="2.2"/></svg>Reach your mobile audience with beautiful HD thumbnails and in-notification videos.</li>
    <li><svg width="14" height="12" viewBox="0 0 14 12"><path d="M1 6l4 4 8-9" fill="none" stroke="#f78f20" stroke-width="2.2"/></svg>Instant video playback, zero buffering, guaranteed flawless playback - even when offline.</li>
    <li><svg width="14" height="12" viewBox="0 0 14 12"><path d="M1 6l4 4 8-9" fill="none" stroke="#f78f20" stroke-width="2.2"/></svg>Content is personalised based on viewer interests and mobile viewing habits.</li>
    <li><svg width="14" height="12" viewBox="0 0 14 12"><path d="M1 6l4 4 8-9" fill="none" stroke="#f78f20" stroke-width="2.2"/></svg>Monetise with beautiful HD preroll or interstitial ads.</li>
    <li><svg width="14" height="12" viewBox="0 0 14 12"><path d="M1 6l4 4 8-9" fill="none" stroke="#f78f20" stroke-width="2.2"/></svg>Easily added to your existing apps within one hour.</li>
  </ul>
</section>

<section class="native">
  <h2 class="abs heading">Native Push Video</h2>
  <p class="abs" style="left:106px;top:226px;width:600px;font-size:13px;color:var(--muted)">Personalised flawless HD videos, discoverable in-app, and playable even when offline.</p>
  <ul class="abs ticks" style="left:106px;top:272px;width:560px;color:var(--muted)">
    <li><svg width="14" height="12" viewBox="0 0 14 12"><path d="M1 6l4 4 8-9" fill="none" stroke="#f78f20" stroke-width="2.2"/></svg>Guarantee your audience never gets frustrated with a poor quality mobile video streaming experience.</li>
    <li><svg width="14" height="12" viewBox="0 0 14 12"><path d="M1 6l4 4 8-9" fill="none" stroke="#f78f20" stroke-width="2.2"/></svg>Instant video playback, zero buffering, HD quality guaranteed - even when offline.</li>
    <li><svg width="14" height="12" viewBox="0 0 14 12"><path d="M1 6l4 4 8-9" fill="none" stroke="#f78f20" stroke-width="2.2"/></svg>Content is personalised based on viewer interests and mobile viewing habits.</li>
    <li><svg width="14" height="12" viewBox="0 0 14 12"><path d="M1 6l4 4 8-9" fill="none" stroke="#f78f20" stroke-width="2.2"/></svg>Monetize with beautiful HD preroll or interstitial ads.</li>
    <li><svg width="14" height="12" viewBox="0 0 14 12"><path d="M1 6l4 4 8-9" fill="none" stroke="#f78f20" stroke-width="2.2"/></svg>Use your existing content management and hosting.</li>
  </ul>
  <div class="device" style="left:880px;top:110px;width:230px;height:440px;background:#eaeaea"></div>
  <div class="device" style="left:795px;top:80px;width:220px;height:460px;background:#1d1d1d;border-color:#111">
    <div class="screen" style="left:14px;top:62px;width:190px;height:330px;background:linear-gradient(180deg,#3a3a3a,#1f1f1f 40%,#4a3b2d)" role="img" aria-label="Video feed app listing music video thumbnails"></div>
  </div>
</section>

<section class="team">
  <h2 class="abs heading">Management Team</h2>
  <span class="abs arrow" style="left:72px">〈</span>
  <span class="abs arrow" style="left:1106px">〉</span>
  <div class="member" style="left:125px"><div class="avatar" role="img" aria-label="Portrait of the CEO"></div><h3>Tom Ellery</h3><p>CEO</p></div>
  <div class="member" style="left:399px"><div class="avatar" role="img" aria-label="Portrait of the CSO"></div><h3>Dean Farrow</h3><p>CSO</p></div>
  <div class="member" style="left:630px"><div class="avatar" role="img" aria-label="Portrait of the CTO"></div><h3>Rob Castell</h3><p>CTO</p></div>
  <div class="member" style="left:879px"><div class="avatar" role="img" aria-label="Portrait of the CTO"></div><h3>Anders</h3><p>CTO</p></div>
</section>

<section class="apps">
  <div class="abs" style="inset:0" role="img" aria-label="Hand holding a smartphone in a dark setting"></div>
  <h2 class="abs heading">Sample Apps</h2>
  <a class="abs store" style="left:392px;top:173px;width:192px;height:66px">
    <svg width="20" height="22" viewBox="0 0 20 22"><rect x="2" y="2" width="16" height="18" rx="3" fill="none" stroke="#fff" stroke-width="2"/></svg>
    <span>Available on the<b>APPVAULT</b></span></a>
  <a class="abs store" style="left:614px;top:173px;width:198px;height:66px">
    <svg width="20" height="22" viewBox="0 0 20 22"><path d="M3 2l15 9-15 9z" fill="#fff"/></svg>
    <span>Available on the<b>PLAYDEPOT</b></span></a>
  <div class="abs field" style="left:182px;top:298px;width:408px;height:46px">Name</div>
  <div class="abs field" style="left:182px;top:366px;width:408px;height:46px">Email</div>
  <div class="abs field" style="left:182px;top:435px;width:408px;height:46px">Subject</div>
  <div class="abs field" style="left:611px;top:298px;width:407px;height:118px">Message:</div>
  <a class="abs btn submit" style="left:611px;top:441px;width:407px;height:46px">SUBMIT NOW</a>
</section>

<section class="features">
  <div class="device" style="left:198px;top:76px;width:222px;height:511px">
    <div class="screen" style="left:14px;top:70px;width:190px;height:342px;background:linear-gradient(180deg,#cfe0ee,#8aa2b5 60%,#b8403c)" role="img" aria-label="Smiling man using a tablet shown on a phone screen"></div>
  </div>
  <h2 class="abs heading">Features</h2>
  <ul class="abs ticks" style="left:526px;top:192px;width:520px">
    <li><svg width="14" height="12" viewBox="0 0 14 12"><path d="M1 6l4 4 8-9" fill="none" stroke="#f78f20" stroke-width="2.2"/></svg>Increase ARPU with new revenue streams.</li>
    <li><svg width="14" height="12" viewBox="0 0 14 12"><path d="M1 6l4 4 8-9" fill="none" stroke="#f78f20" stroke-width="2.2"/></svg>Velmora Media is a content platform for operators, that allows them to create new business models based on mobile video.</li>
    <li><svg width="14" height="12" viewBox="0 0 14 12"><path d="M1 6l4 4 8-9" fill="none" stroke="#f78f20" stroke-width="2.2"/></svg>Velmora's platforms predictively pre-positions video content, and uses ML to reveal video at the perfect moment for maximum engagement.</li>
    <li><svg width="14" height="12" viewBox="0 0 14 12"><path d="M1 6l4 4 8-9" fill="none" stroke="#f78f20" stroke-width="2.2"/></svg>One of the common solutions is a "value exchange", where the consumers receive data or dollars off their bill, in exchange for viewing promotional content.</li>
    <li><svg width="14" height="12" viewBox="0 0 14 12"><path d="M1 6l4 4 8-9" fill="none" stroke="#f78f20" stroke-width="2.2"/></svg>The type of content we see as most effective is native vertical video. Think of Flashgram 3V ads, but published directly to the phone, rather than a specific app.</li>
  </ul>
</section>

<footer class="footer">
  <div class="brand"><span class="brand-mark"></span>velmora</div>
  <div class="abs foot-links"><span>PRODUCT</span><span>/</span><span>CONTACT</span><span>/</span><span>BLOG</span><span>/</span><span>ABOUT</span><span>/</span><span>LOGIN</span></div>
  <div class="abs foot-copy"><span>© 2016 Velmora Media, Inc.</span><span>Terms &amp; Conditions</span><span>Privacy Policy</span></div>
  <div class="abs social"><span></span><span></span><span></span></div>
  <span class="abs foot-tag">CS</span>
</footer>

</body>
</html>
```